post card 4x6

this is a post card that will be sent to plumbing companies and foundation repair companies for whole sale work. if you can add ( work done in unmarked truck -will ware your shirt)

```html
<!DOCTYPE html>
<html lang="en">
<head>
<meta charset="utf-8">
<title>DrainView Postcard</title>
<link rel="stylesheet" href="https://fonts.googleapis.com/css2?family=Oswald:wght@700&family=Poppins:wght@300;400;500;600;700;800&display=swap">
<style>
  :root {
    --navy: #2b3446;
    --red: #e8473e;
    --ink: #2a2f3a;
    --white: #ffffff;
    --paper: #f3f3f1;
    --rule: #9a9a9a;
    --stamp: #e6e6e6;
  }
  * { box-sizing: border-box; margin: 0; padding: 0; }
  html, body { width: 1200px; height: 2534px; overflow: hidden; }
  body {
    background: var(--paper);
    font-family: "Poppins", sans-serif;
    color: var(--ink);
    position: relative;
  }
  .card {
    position: absolute;
    left: 147px;
    width: 906px;
    height: 605px;
    overflow: hidden;
    box-shadow: 0 6px 14px rgba(0,0,0,0.18);
  }
  .card--front { top: 380px; }
  .card--back { top: 1420px; }
  .card__art { position: absolute; inset: 0; }
  .abs { position: absolute; }

  /* front */
  .brand {
    font-family: "Poppins", sans-serif;
    font-weight: 800;
    color: var(--red);
    letter-spacing: -0.5px;
    line-height: 1;
  }
  .front .brand { left: 135px; top: 42px; font-size: 52px; }
  .tagline { left: 130px; top: 132px; font-size: 25px; font-weight: 500; color: var(--ink); }
  .headline {
    left: 128px; top: 168px;
    font-family: "Oswald", sans-serif; font-weight: 700;
    font-size: 58px; line-height: 61px; text-transform: uppercase;
  }
  .headline .red { color: var(--red); }
  .headline .dark { color: var(--ink); }
  .headline .amp { font-family: "Poppins", sans-serif; font-weight: 300; color: var(--red); font-size: 58px; }
  .features {
    left: 132px; top: 364px;
    display: grid; grid-template-columns: 260px 260px; row-gap: 5px;
    list-style: none; font-size: 15.5px; font-weight: 500; color: var(--ink);
  }
  .features li, .service__title { display: flex; align-items: center; gap: 8px; }
  .tick { width: 15px; height: 15px; flex: none; }
  .slogan {
    left: 150px; top: 451px; width: 560px;
    font-size: 24px; font-weight: 700; color: var(--white); white-space: nowrap;
  }
  .slogan .dollar { color: var(--navy); }
  .cta-label { font-size: 18px; font-weight: 600; color: var(--white); text-transform: uppercase; white-space: nowrap; }
  .cta-label .hl { color: var(--red); }
  .phone {
    display: flex; align-items: center; gap: 10px;
    font-size: 38px; font-weight: 700; color: var(--white); line-height: 1;
  }
  .phone svg { width: 24px; height: 24px; }
  .front .cta-label { left: 42px; top: 506px; }
  .front .phone { left: 44px; top: 534px; }
  .divider { left: 357px; top: 510px; width: 2px; height: 62px; background: var(--white); }
  .license {
    border: 2px solid var(--white); color: var(--white);
    font-weight: 600; text-align: center; line-height: 1;
  }
  .front .license { left: 373px; top: 510px; width: 240px; height: 38px; font-size: 25px; padding-top: 5px; }
  .web { font-size: 17px; font-weight: 600; color: var(--white); white-space: nowrap; }
  .web .hl { color: var(--red); }
  .front .web { left: 373px; top: 554px; font-size: 14.5px; }
  .thumb { top: 497px; width: 112px; height: 94px; border-radius: 6px; border: 2px solid #4a5468; }
  .thumb--pipe { left: 626px; background: radial-gradient(circle at 40% 45%, #2a1a12 0 12%, #7a5334 35%, #a67a55 70%, #5e4028 100%); }
  .thumb--liner { left: 749px; background: radial-gradient(circle at 45% 45%, #1d3a2a 0 8%, #3f8a5f 30%, #5bae7c 65%, #2d6a47 100%); }

  /* back */
  .about-title, .services-title { left: 43px; font-size: 26px; font-weight: 600; color: var(--white); line-height: 1.2; }
  .about-title .hl, .services-title .hl { color: var(--red); }
  .about-title { top: 38px; }
  .about-copy { left: 43px; top: 80px; width: 380px; font-size: 11px; line-height: 13px; color: var(--white); font-weight: 400; }
  .services-title { top: 164px; }
  .services { left: 43px; top: 205px; width: 300px; list-style: none; color: var(--white); }
  .service { margin-bottom: 6px; }
  .service__title { font-size: 17px; font-weight: 500; line-height: 22px; }
  .service__desc { font-size: 11px; line-height: 12.5px; margin-top: 1px; }
  .back .license { left: 43px; top: 443px; width: 152px; height: 34px; font-size: 18px; padding-top: 6px; border-color: var(--red); }
  .back .cta-label { left: 42px; top: 490px; font-size: 19px; }
  .back .cta-label .hl { color: var(--navy); }
  .back .phone { left: 44px; top: 518px; }
  .back .web { left: 43px; top: 556px; }
  .back .web .hl { color: var(--white); }
  .back .brand { left: 525px; top: 48px; font-size: 38px; }
  .truck-note { left: 527px; top: 98px; width: 240px; font-size: 13px; line-height: 17px; font-weight: 500; color: var(--navy); }
  .truck-note .hl { color: var(--red); font-weight: 600; }
  .stamp { left: 791px; top: 42px; width: 70px; height: 75px; background: var(--stamp); }
  .address-line { left: 524px; width: 338px; height: 1px; background: var(--rule); }
</style>
</head>
<body>

<!-- Front side -->
<section class="card card--front front">
  <svg class="card__art" viewBox="0 0 906 605" width="906" height="605">
    <defs>
      <linearGradient id="waterFlow" x1="0" y1="0" x2="0" y2="1">
        <stop offset="0" stop-color="#4a5567"/>
        <stop offset="0.5" stop-color="#7d8a9b"/>
        <stop offset="1" stop-color="#3a4457"/>
      </linearGradient>
      <linearGradient id="workshop" x1="0" y1="0" x2="1" y2="1">
        <stop offset="0" stop-color="#d9d8d4"/>
        <stop offset="0.5" stop-color="#a9acb2"/>
        <stop offset="1" stop-color="#5f6874"/>
      </linearGradient>
    </defs>
    <rect width="906" height="605" fill="var(--navy)"/>
    <g role="img" aria-label="Photo of water flowing from a pipe outlet">
      <rect x="0" y="0" width="150" height="487" fill="url(#waterFlow)"/>
    </g>
    <g role="img" aria-label="Photo of a gloved plumber fitting a chrome faucet held in a bench vise, with brass valves">
      <path d="M488 0 H906 V487 H740 C640 420 560 310 522 190 C502 120 490 60 488 0 Z" fill="url(#workshop)"/>
    </g>
    <path d="M130 0 H488 C490 60 502 120 522 190 C560 310 640 420 740 487 H138 C100 400 78 300 80 210 C82 120 100 55 130 0 Z" fill="var(--white)"/>
    <path d="M128 446 H700 L738 487 H140 Z" fill="var(--red)"/>
  </svg>

  <div class="abs brand">DrainView</div>
  <p class="abs tagline">Your One-Stop Solution for</p>
  <h1 class="abs headline">
    <span class="red">Plumbing</span> <span class="amp">&amp;</span><br>
    <span class="dark">Irrigation</span><br>
    <span class="red">Installation</span>
  </h1>
  <ul class="abs features">
    <li><svg class="tick" viewBox="0 0 16 16"><circle cx="8" cy="8" r="8" fill="#8b8f97"/><path d="M4.5 8.2 7 10.6 11.5 5.6" fill="none" stroke="#fff" stroke-width="2"/></svg>CIPP (Curved in place pipe)</li>
    <li><svg class="tick" viewBox="0 0 16 16"><circle cx="8" cy="8" r="8" fill="#8b8f97"/><path d="M4.5 8.2 7 10.6 11.5 5.6" fill="none" stroke="#fff" stroke-width="2"/></svg>SIPP (Spray in place pipe)</li>
    <li><svg class="tick" viewBox="0 0 16 16"><circle cx="8" cy="8" r="8" fill="#8b8f97"/><path d="M4.5 8.2 7 10.6 11.5 5.6" fill="none" stroke="#fff" stroke-width="2"/></svg>HYDRO JETTING</li>
    <li><svg class="tick" viewBox="0 0 16 16"><circle cx="8" cy="8" r="8" fill="#8b8f97"/><path d="M4.5 8.2 7 10.6 11.5 5.6" fill="none" stroke="#fff" stroke-width="2"/></svg>SEWER CAMERA &amp; LOCATE</li>
    <li><svg class="tick" viewBox="0 0 16 16"><circle cx="8" cy="8" r="8" fill="#8b8f97"/><path d="M4.5 8.2 7 10.6 11.5 5.6" fill="none" stroke="#fff" stroke-width="2"/></svg>PIPE BURSTING</li>
    <li><svg class="tick" viewBox="0 0 16 16"><circle cx="8" cy="8" r="8" fill="#8b8f97"/><path d="M4.5 8.2 7 10.6 11.5 5.6" fill="none" stroke="#fff" stroke-width="2"/></svg>RESIZE CAST IRON</li>
  </ul>
  <p class="abs slogan">YOU MAKE THE <span class="dollar">$</span> WE DO THE WORK</p>

  <p class="abs cta-label">Call for <span class="hl">Whole Sale Pricing</span></p>
  <p class="abs phone">
    <svg viewBox="0 0 24 24"><path d="M6.6 2.5 9.4 6.4 7.6 8.6c1.2 2.9 3.9 5.6 6.8 6.8l2.2-1.8 3.9 2.8-1.4 3.6c-8.6.4-15.9-6.9-15.5-15.5Z" fill="var(--red)"/></svg>
    555-210-4477
  </p>
  <div class="abs divider"></div>
  <div class="abs license">RMP#10382</div>
  <p class="abs web">www.<span class="hl">drainviewplumbing</span>.com</p>
  <div class="abs thumb thumb--pipe" role="img" aria-label="Camera view inside a corroded sewer pipe"></div>
  <div class="abs thumb thumb--liner" role="img" aria-label="Camera view inside a newly lined green pipe"></div>
</section>

<!-- Back side -->
<section class="card card--back back">
  <svg class="card__art" viewBox="0 0 906 605" width="906" height="605">
    <rect width="906" height="605" fill="var(--white)"/>
    <path d="M0 0 H493 C452 120 420 260 404 380 L398 478 H0 Z" fill="var(--navy)"/>
    <path d="M0 478 H398 C418 540 452 582 493 605 H0 Z" fill="var(--red)"/>
    <g>
      <circle cx="399" cy="258" r="52" fill="var(--red)"/>
      <circle cx="392" cy="357" r="52" fill="var(--red)"/>
      <circle cx="408" cy="454" r="52" fill="var(--red)"/>
      <circle cx="440" cy="550" r="52" fill="var(--red)"/>
    </g>
    <g role="img" aria-label="Photo of a technician working on drain cleaning equipment">
      <circle cx="396" cy="258" r="45" fill="#6f6a62"/>
    </g>
    <g role="img" aria-label="Photo of a pipe bursting head in soil">
      <circle cx="389" cy="357" r="45" fill="#5a534b"/>
    </g>
    <g role="img" aria-label="Photo of a pipe being relined">
      <circle cx="405" cy="454" r="45" fill="#8d929a"/>
    </g>
    <g role="img" aria-label="Photo of a technician running a sewer inspection camera">
      <circle cx="437" cy="550" r="45" fill="#3d4658"/>
    </g>
  </svg>

  <h2 class="abs about-title">About <span class="hl">DrainView</span></h2>
  <p class="abs about-copy">DrainView is a family owned and operated plumbing business specializing in trenchless lining &amp; camera location. We can locate &amp; show you the exact problem andoffer you the best solution for fixing it. The best solution can range from traditional dig up and replace to pipe lining the sewer, whichever procedure meets the job needs. We give you the choice many others do not have available!</p>

  <h2 class="abs services-title">Our <span class="hl">Services</span></h2>
  <ul class="abs services">
    <li class="service">
      <p class="service__title"><svg class="tick" viewBox="0 0 16 16"><circle cx="8" cy="8" r="8" fill="#b9bdc5"/><path d="M4.5 8.2 7 10.6 11.5 5.6" fill="none" stroke="var(--navy)" stroke-width="2"/></svg>Drain Cleaning</p>
      <p class="service__desc">Cedar County's best when it comes to drain cleaning and drain repair.</p>
    </li>
    <li class="service">
      <p class="service__title"><svg class="tick" viewBox="0 0 16 16"><circle cx="8" cy="8" r="8" fill="#b9bdc5"/><path d="M4.5 8.2 7 10.6 11.5 5.6" fill="none" stroke="var(--navy)" stroke-width="2"/></svg>Pipe Bursting</p>
      <p class="service__desc">Pipe bursting replaces old, unusable piping without tearing up the yard.</p>
    </li>
    <li class="service">
      <p class="service__title"><svg class="tick" viewBox="0 0 16 16"><circle cx="8" cy="8" r="8" fill="#b9bdc5"/><path d="M4.5 8.2 7 10.6 11.5 5.6" fill="none" stroke="var(--navy)" stroke-width="2"/></svg>Pipe Lining</p>
      <p class="service__desc">Pipe lining relines your existing pipes with a brand new pipe inside.</p>
    </li>
    <li class="service">
      <p class="service__title"><svg class="tick" viewBox="0 0 16 16"><circle cx="8" cy="8" r="8" fill="#b9bdc5"/><path d="M4.5 8.2 7 10.6 11.5 5.6" fill="none" stroke="var(--navy)" stroke-width="2"/></svg>Video Inspection</p>
      <p class="service__desc">Let DrainView's technicians SHOW you<br>exactly what is wrong with your pipes. inside.</p>
    </li>
  </ul>

  <div class="abs license">RMP#10382</div>
  <p class="abs cta-label">Call for <span class="hl">Whole Sale Pricing</span></p>
  <p class="abs phone">
    <svg viewBox="0 0 24 24"><path d="M6.6 2.5 9.4 6.4 7.6 8.6c1.2 2.9 3.9 5.6 6.8 6.8l2.2-1.8 3.9 2.8-1.4 3.6c-8.6.4-15.9-6.9-15.5-15.5Z" fill="var(--navy)"/></svg>
    555-210-4477
  </p>
  <p class="abs web">www.<span class="hl">drainviewplumbing</span>.com</p>

  <div class="abs brand">DrainView</div>
  <p class="abs truck-note">Work done in an <span class="hl">unmarked truck</span> &mdash; we will wear <span class="hl">your shirt</span>.</p>
  <div class="abs stamp"></div>
  <div class="abs address-line" style="top:323px"></div>
  <div class="abs address-line" style="top:386px"></div>
  <div class="abs address-line" style="top:452px"></div>
</section>

</body>
</html>
```